New Wrestling company needs a website

We need a website design for a new wrestling company in Australia that will be running 3-4 events per year. Wrestling company is Summit Grip Wrestling (SGW).

The design of the logo is in place and can be provided, and I have purchased the website domain.

A detailed description of the intent and purpose of this company can be provided.

The aim would be to have around 5 specific pages on SGW, with two standard “about” and “contact” pages. E.g.
- About SGW (focus and purpose of the company)
- SGW Events (specific focus on events run by SGW)
- SGW News (news and stories on wrestling’s across Oceania)
- SGW Media (where to watch SGW and our partners))
- SGW Partners and Sponsors (partner and affiliate information)
- SGW Power Rankings (top 10 ranked wrestlers from Oceania which is updated weekly)
- SGW fans (highlighting how to become part of SGW as a fan)
- Contact SGW
Updates

The logo design should now be included in the brief, please feel free to reach out to me directly if you can't access it or require any other information.

Target Market(s)

Wrestling Fans

Industry/Entity Type

Sport / Wrestling

Coding

Coded - Design and coding required

Number of Pages Required

5+ page

Requirements
Must have
• A Wrestling and or Sports feel to the website design

```html
<!DOCTYPE html>
<html lang="en">
<head>
<meta charset="utf-8">
<title>Summit Grip Wrestling</title>
<link rel="stylesheet" href="https://fonts.googleapis.com/css2?family=Montserrat:wght@500;700;800&family=IBM+Plex+Sans:wght@400;500&display=swap">
<style>
:root{
  --black:#000;
  --white:#fff;
  --ink:#1b1b1b;
  --body:#2a2a2a;
  --accent:#2a9fe0;
  --band:#2b6cc4;
  --muted:#f1f0f3;
  --line:#e3e3e6;
  --row:#f4f4f6;
}
*{box-sizing:border-box;margin:0;padding:0}
html,body{width:1200px;height:3335px;overflow:hidden}
body{font-family:"IBM Plex Sans",Arial,sans-serif;color:var(--body);background:var(--white);position:relative}
.head{font-family:"Montserrat",Arial,sans-serif;font-weight:800;color:var(--ink);text-transform:uppercase}
.rule{display:block;width:90px;height:2px;background:var(--accent);margin-top:14px}
.center{text-align:center}
.center .rule{margin:16px auto 0}
.btn{display:inline-block;background:var(--accent);color:var(--white);font-family:"Montserrat",Arial,sans-serif;font-weight:700;text-transform:uppercase;text-decoration:none}
.shot{display:block}

/* hero */
.hero{position:relative;height:682px;background:var(--black);overflow:hidden}
.hero-floor{position:absolute;left:0;right:0;top:468px;bottom:0;background:linear-gradient(180deg,#1b3f9a,#16307a 60%,#1d3680)}
.hero-photo{position:absolute;left:520px;top:80px;width:620px;height:600px;background:radial-gradient(ellipse at 50% 45%,#5a4a48 0%,#3a2a2c 35%,rgba(0,0,0,0) 70%)}
.brand{position:absolute;display:flex;align-items:center;gap:8px;color:#3aa8e8;font-family:"Montserrat",Arial,sans-serif;font-weight:800}
.brand .dot{width:22px;height:22px;border-radius:50%;background:#3aa8e8}
.hero .brand{left:36px;top:36px;font-size:40px}
.nav{position:absolute;right:26px;top:26px;display:flex;gap:37px;list-style:none}
.nav a{color:var(--white);text-decoration:none;font-size:13px;letter-spacing:.6px;text-transform:uppercase}
.hero-copy{position:absolute;left:105px;top:203px;color:var(--white)}
.hero-copy .kicker{font-family:"Montserrat",Arial,sans-serif;font-weight:500;font-size:24px;letter-spacing:1px}
.hero-copy h1{font-family:"Montserrat",Arial,sans-serif;font-weight:800;font-size:44px;line-height:53px;margin-top:14px;text-transform:uppercase}
.hero-copy .btn{margin-top:30px;padding:12px 20px;font-size:15px}
.dots{position:absolute;left:563px;top:646px;display:flex;gap:10px}
.dots span{width:7px;height:7px;border-radius:50%;background:var(--white)}
.dots span.on{background:var(--accent)}

/* about */
.about{position:relative;height:484px}
.about-photo{position:absolute;left:133px;top:50px;width:433px;height:362px;background:linear-gradient(135deg,#3b47a8,#5a63c6 50%,#8e3a3a)}
.about-inset{position:absolute;left:364px;top:206px;width:230px;height:230px;border-radius:50%;border:8px solid var(--white);background:linear-gradient(135deg,#1f3fc0,#2a55d6 60%,#c43a3a)}
.about-copy{position:absolute;left:629px;top:50px;width:440px}
.about-copy h2{font-size:24px}
.about-copy p{margin-top:34px;font-size:15px;line-height:23.2px}
.about-copy .btn{margin-top:40px;margin-left:3px;padding:12px 17px;font-size:13px}

/* events */
.events{height:582px;background:var(--muted);padding-top:48px}
.events h2{font-size:24px}
.cards{display:flex;gap:22px;margin:36px 0 0 133px}
.card{width:297px;height:424px;background:var(--white);box-shadow:0 1px 4px rgba(0,0,0,.08)}
.card-photo{position:relative;height:196px}
.date{position:absolute;left:27px;bottom:0;width:48px;height:48px;background:var(--white);text-align:center;font-size:10px;padding-top:8px;color:var(--ink)}
.date b{display:block;font-weight:500;font-size:17px}
.card-body{padding:30px 28px 0}
.card-body h3{font-family:"Montserrat",Arial,sans-serif;font-weight:500;font-size:15px;line-height:19px;color:var(--ink)}
.card-body p{margin-top:14px;font-size:12px;line-height:17.5px}
.card-body .btn{margin-top:19px;padding:8px 12px;font-size:9.5px}

/* media */
.media{position:relative;height:510px;background:linear-gradient(135deg,#eef0f5,#e4e7ef 50%,#f0eef2);padding-top:58px}
.media h2{font-size:24px}
.videos{display:flex;gap:20px;margin:40px 0 0 132px}
.video{position:relative;width:458px;height:330px}
.play{position:absolute;left:50%;top:50%;width:52px;height:52px;margin:-26px 0 0 -26px}

/* rankings */
.rankings{height:447px;padding-top:55px}
.rankings h2{font-size:24px}
.table{margin:34px 0 0 220px;width:761px;border-collapse:collapse;box-shadow:0 1px 4px rgba(0,0,0,.08);font-size:14px;text-align:center}
.table th{background:var(--accent);color:var(--white);font-family:"Montserrat",Arial,sans-serif;font-weight:700;font-size:13px;height:38px;border-right:2px solid var(--white)}
.table td{height:44px;border-right:1px solid var(--line);color:var(--ink)}
.table tr:nth-child(even) td{background:var(--row)}
.table th:last-child,.table td:last-child{border-right:0}

/* fans */
.fans{height:298px;background:linear-gradient(135deg,#2866c0,#2f72cc 50%,#2560b8);color:var(--white);padding-top:66px}
.fans h2{color:var(--white);font-size:27px}
.fans p{margin:14px auto 0;width:700px;font-size:17px;line-height:26px}
.fans .btn{margin-top:26px;padding:14px 30px;font-size:16px}

/* footer */
.footer{position:relative;height:332px;background:var(--black);color:var(--white)}
.footer .brand{left:136px;top:84px;font-size:34px}
.col{position:absolute;top:44px}
.col h4{font-family:"Montserrat",Arial,sans-serif;font-weight:700;font-size:12px;letter-spacing:.4px;text-transform:uppercase}
.menu{list-style:none;margin-top:20px}
.menu li{font-size:11.5px;line-height:20px;text-transform:uppercase}
.info{margin-top:20px}
.info div{display:flex;gap:12px;font-size:11.5px;line-height:15px;margin-bottom:21px}
.info svg{flex:none}
.copy{position:absolute;left:137px;right:137px;top:262px;border-top:1px solid #333;text-align:center;padding-top:42px;font-size:9.5px;color:#ccc}
</style>
</head>
<body>

<header class="hero">
  <div class="hero-floor"></div>
  <div class="hero-photo shot" role="img" aria-label="Two wrestlers grappling on a blue mat"></div>
  <div class="brand"><span class="dot"></span>SGW</div>
  <ul class="nav">
    <li><a href="#">About SGW</a></li><li><a href="#">Events</a></li><li><a href="#">News</a></li><li><a href="#">Media</a></li><li><a href="#">Partners</a></li><li><a href="#">Power Rankings</a></li><li><a href="#">Fans</a></li><li><a href="#">Contact SGW</a></li>
  </ul>
  <div class="hero-copy">
    <div class="kicker">WELCOME TO</div>
    <h1>Summit Grip<br>Wrestling</h1>
    <a class="btn" href="#">Read More</a>
  </div>
  <div class="dots"><span></span><span></span><span class="on"></span><span></span><span></span></div>
</header>

<section class="about">
  <div class="about-photo shot" role="img" aria-label="Wrestlers in red and blue locked on the mat"></div>
  <div class="about-inset shot" role="img" aria-label="Wrestler executing a throw on a blue mat"></div>
  <div class="about-copy">
    <h2 class="head">About SGW</h2><span class="rule"></span>
    <p>Sed ut perspiciatis unde omnis iste natus error sit voluptatem accusantium doloremque laudantium, totam rem aperiam, eaque ipsa quae ab illo inventore veritatis et quasi architecto beatae vitae dicta sunt explicabo. Nemo enim ipsam voluptatem quia voluptas sit aspernatur aut odit aut fugit, sed quia consequuntur magni dolores eos qui ratione voluptatem sequi nesciunt. Neque porro quisquam est, qui dolorem ipsum quia dolor sit amet, consectetur, adipisci velit, sed quia non numquam eius modi tempora incidunt ut labore.</p>
    <a class="btn" href="#">Read More</a>
  </div>
</section>

<section class="events">
  <div class="center"><h2 class="head">SGW Events</h2><span class="rule"></span></div>
  <div class="cards">
    <article class="card">
      <div class="card-photo shot" role="img" aria-label="Two wrestlers shaking hands before a bout" style="background:linear-gradient(90deg,#2a3a8a,#6a2a30 50%,#b83030)"><div class="date">JAN<b>11</b></div></div>
      <div class="card-body"><h3>Sed ut perspiciatis unde omnis iste natus</h3><p>Nemo enim ipsam voluptatem quia voluptas sit aspernatur aut odit aut fugit, sed quia consequuntur magni dolores eos qui error sit voluptatem.</p><a class="btn" href="#">Read More</a></div>
    </article>
    <article class="card">
      <div class="card-photo shot" role="img" aria-label="Wrestler lifted high in a gym hall" style="background:linear-gradient(180deg,#4a5058,#6a7480 60%,#3a4a7a)"><div class="date">JAN<b>11</b></div></div>
      <div class="card-body"><h3>Lorem ipsum dolor sit ametconsectetur</h3><p>Nemo enim ipsam voluptatem quia voluptas sit aspernatur aut odit aut fugit, sed quia consequuntur magni dolores eos qui error sit voluptatem.</p><a class="btn" href="#">Read More</a></div>
    </article>
    <article class="card">
      <div class="card-photo shot" role="img" aria-label="Wrestlers grappling under spotlights" style="background:radial-gradient(ellipse at 50% 50%,#4a4458,#1a1a22 70%)"><div class="date">JAN<b>11</b></div></div>
      <div class="card-body"><h3>On the other hand we denounce with righteous</h3><p>Nemo enim ipsam voluptatem quia voluptas sit aspernatur aut odit aut fugit, sed quia consequuntur magni dolores eos qui error sit voluptatem.</p><a class="btn" href="#">Read More</a></div>
    </article>
  </div>
</section>

<section class="media">
  <div class="center"><h2 class="head">SGW Media</h2><span class="rule"></span></div>
  <div class="videos">
    <div class="video shot" role="img" aria-label="Video still of two wrestlers tied up in front of a crowd" style="background:linear-gradient(180deg,#6a5040,#8a6a48 45%,#3a4a78)">
      <svg class="play" viewBox="0 0 52 52"><circle cx="26" cy="26" r="24" fill="#fff"/><circle cx="26" cy="26" r="19" fill="#2a9fe0"/><path d="M21 16 L36 26 L21 36 Z" fill="#fff"/></svg>
    </div>
    <div class="video shot" role="img" aria-label="Video still of a wrestler lifting an opponent under spotlights" style="background:radial-gradient(ellipse at 50% 45%,#4a4450,#141418 70%)">
      <svg class="play" viewBox="0 0 52 52"><circle cx="26" cy="26" r="24" fill="#fff"/><circle cx="26" cy="26" r="19" fill="#2a9fe0"/><path d="M21 16 L36 26 L21 36 Z" fill="#fff"/></svg>
    </div>
  </div>
</section>

<section class="rankings">
  <div class="center"><h2 class="head">SGW Power Rankings</h2><span class="rule"></span></div>
  <table class="table">
    <colgroup><col style="width:165px"><col style="width:270px"><col style="width:175px"><col></colgroup>
    <tr><th>RANK</th><th>TEAM</th><th>RECORD</th><th>POINTS</th></tr>
    <tr><td>1</td><td>Ridgeback (11)</td><td>6-0</td><td>355</td></tr>
    <tr><td>2</td><td>Harbour State (3)</td><td>3-2</td><td>420</td></tr>
    <tr><td>3</td><td>Northvale</td><td>1-0</td><td>110</td></tr>
    <tr><td>4</td><td>Richard</td><td>2-0</td><td>987</td></tr>
    <tr><td>5</td><td>Ferando</td><td>6-0</td><td>521</td></tr>
  </table>
</section>

<section class="fans center">
  <h2 class="head">How to become part of SGW as a fan</h2>
  <p>Nemo enim ipsam voluptatem quia voluptas sit aspernatur aut odit aut fugit, sed quia consequuntur magni dolores eos qui error sit voluptatem.</p>
  <a class="btn" href="#">Join Now</a>
</section>

<footer class="footer">
  <div class="brand"><span class="dot"></span>SGW</div>
  <div class="col" style="left:393px">
    <h4>Menu</h4>
    <ul class="menu"><li>About SGW</li><li>Events</li><li>News</li><li>Media</li><li>Partners</li><li>Power Rankings</li><li>Fans</li><li>Contact SGW</li></ul>
  </div>
  <div class="col" style="left:657px">
    <h4>Contact Us</h4>
    <div class="info">
      <div><svg width="22" height="22" viewBox="0 0 22 22"><circle cx="11" cy="11" r="11" fill="#fff"/><path d="M11 5a4 4 0 0 0-4 4c0 3 4 8 4 8s4-5 4-8a4 4 0 0 0-4-4z" fill="#000"/><circle cx="11" cy="9" r="1.5" fill="#fff"/></svg><span>27 Ridgeline Road<br>Katoomba NSW 2780</span></div>
      <div><svg width="22" height="22" viewBox="0 0 22 22"><circle cx="11" cy="11" r="11" fill="#fff"/><path d="M7.5 6h2l1 2.5-1.3 1a6 6 0 0 0 3.3 3.3l1-1.3 2.5 1v2a1 1 0 0 1-1 1A8.5 8.5 0 0 1 6.5 7a1 1 0 0 1 1-1z" fill="#000"/></svg><span>Call Us<br>02 5550 1942</span></div>
      <div><svg width="22" height="22" viewBox="0 0 22 22"><circle cx="11" cy="11" r="11" fill="#fff"/><rect x="6" y="7.5" width="10" height="7" fill="#000"/><path d="M6 7.5l5 4 5-4" stroke="#fff" fill="none"/></svg><span>E mail Us<br>info@summitgrip.com</span></div>
    </div>
  </div>
  <div class="col" style="left:966px">
    <h4>Follow Us</h4>
    <div class="info">
      <div><svg width="22" height="22" viewBox="0 0 22 22"><circle cx="11" cy="11" r="11" fill="#fff"/></svg><span>Like us on<br>FANPAGE</span></div>
      <div><svg width="22" height="22" viewBox="0 0 22 22"><circle cx="11" cy="11" r="11" fill="#fff"/></svg><span>Follow us on<br>NEWSFEED</span></div>
      <div><svg width="22" height="22" viewBox="0 0 22 22"><circle cx="11" cy="11" r="11" fill="#fff"/></svg><span>Follow us on<br>NETWORK</span></div>
    </div>
  </div>
  <div class="copy">Copyright © 2022 All Rights Reserved</div>
</footer>

</body>
</html>
```